LIFE CHANGING NEW WEBSITE DESIGN NEEDED FOR FULL WEBSITE- FUN/FEMININE!

I need a website designed for a personal financial advice website geared at women called BLUE OTTER LANTERN. I will be providing free financial advice around topics of making, saving, spending and sharing money. The concept is to change the way women understand money and the necessity around building various passive income streams to ensure full financial freedom. This will then carry down to advice for mothers with children and children in particular. The website should be elegant and yet witty. I don't want lots of serious photos but more relatable. I will have a photo of myself and my story as this is a blog and needs to be relatable to women and mothers. I like pinks and greys. I want to have a pink piggy bank being broken with a hammer in the front screen to break our traditional mindset around piggy bank saving/spending habits. I have created a logo that is a pink piggy head with BLUE OTTER LANTERN that needs to be incorporated so that it blends into the heading. I have also already started designing the website on Squarespace and can provide access to that. Basically it should have a format of BLUE OTTER LANTERN LOGO center in header then on left hand navigation: MAKE, SAVE, SPEND, SHARE then on right hand header navigation: MISSION, GET STARTED, CONTACT BOL I would like to have the front page when you go to the url to have the image of the piggy bank being broken then a catchy phrase then under 4 boxes with MAKE (image and description) SAVE (image and description) SPEND (image and description) SHARE (image and description) if you click on those or the title they go to pages that are dedicated to each them. Each page should have a little intro on the topic then I want lots of blog links as I will be mainly writing blogs. Each blog site should have ability to write comments as well. I need social media icons on each page too. Please let me know what you need from me to get started. I prefer having a discussion if possible to not waste anyone's time. I need the site to be easy for me to use and add blogs/urls etc as needed. I also need the site to be put into my domain that I already purchased: www.blueotterlantern-sample.com

Target Market(s)

teenage girls, 20 something girls, 30 something girls and mothers

Coding

Coded - Design and coding required

Number of Pages Required

5+ page

Font styles to use
Sans Serif

Colors
e667a6
e34197
f59195
eea4c8
aaaaaa
cbcbcb
959595

Requirements
Must have
• TOP NAVIGATION
• MAKE SAVE SPEND SHARE LOGO/BLUE OTTER LANTERN MISSION GET STARTED CONTACT BOL
• FRONT PAGE: IMAGE OF PIGGY BANK BEING BROKEN WITH A HAMMER
• CATCH PHRASE OVER THE IMAGE
• BUTTON IN PINK- TAKE ACTION (WHICH DIRECTS TO TAKE ACTION TAB ON NAVIGATION HEADER
• 4 BOXES BELOW MAIN IMAGE WITH IMAGE/DESCRIPTIONS FOR MAKE, SAVE, SPEND, SHARE THAT EACH GO TO THE PAGES FROM THE NAVIGATION HEADER
• EACH PAGE SHOULD BE DEDICATED TO THOSE TOPICS THEN THERE IS AN INTRO ON EACH PAGE THEN THE LINKS TO DIFFERENT BLOGS AROUND EACH TOPIC FOR MAKE, SAVE, SPEND, SHARE
• EACH BLOG SHOULD HAVE COMMENTS SECTION AND SOCIAL MEDIA ICONS
• (GOOD TO USE PINKS/GREYS)
Should not have
• BE SUPER BUSY, CLUTTERED, FEEL LIKE I AM SELLING SOMETHING

```html
<!DOCTYPE html>
<html lang="en">
<head>
<meta charset="utf-8">
<title>Blue Otter Lantern</title>
<link href="https://fonts.googleapis.com/css2?family=Quicksand:wght@500;600&family=Roboto:wght@400;500&display=swap" rel="stylesheet">
<style>
:root{
  --pink:#e34197;
  --pink-soft:#ee6fb0;
  --pink-pale:#eea4c8;
  --grey-band:#ececec;
  --grey-text:#959595;
  --ink:#222;
  --footer:#231f20;
  --white:#fff;
}
*{margin:0;padding:0;box-sizing:border-box}
html,body{width:1200px;height:3647px;overflow:hidden}
body{position:relative;background:var(--white);font-family:"Roboto",sans-serif;color:var(--ink)}
.abs{position:absolute}
.center{text-align:center}
.brand{font-family:"Quicksand",sans-serif;font-weight:500;color:var(--pink)}
.brand-mark{border:3px solid var(--pink);border-radius:50%;position:absolute}

/* header */
.site-header{position:absolute;left:0;top:0;width:1200px;height:134px;border-bottom:1px solid #e6e6e6;background:var(--white)}
.nav a{position:absolute;top:56px;font-size:17px;color:#333;text-decoration:none}
.header-brand{left:0;width:1200px;top:80px;font-size:35px}

/* hero */
.hero{left:0;top:134px;width:1200px;height:637px;background:linear-gradient(90deg,#ece9ec,#e4e1e5)}
.hero-photo{left:0;top:134px;width:640px;height:620px;background:radial-gradient(circle at 62% 70%,#f07ab0 0 18%,transparent 19%),linear-gradient(120deg,#f4f3f4 0%,#dcd9dc 55%,#e8e5e8 100%)}
.hero-title{left:600px;width:550px;top:325px;font-size:35px}
.hero-text{left:600px;width:550px;top:384px;font-size:17px;line-height:35px;color:#222}
.btn{position:absolute;background:var(--pink);color:var(--white);border-radius:30px;font-family:"Quicksand",sans-serif;font-weight:600;display:flex;align-items:center;justify-content:center;gap:8px}
.btn svg{width:18px;height:18px}

/* welcome */
.section-title{left:0;width:1200px;font-family:"Quicksand",sans-serif;font-weight:500}
.welcome-text{left:120px;width:960px;top:926px;font-size:15px;line-height:32px;color:#222}
.topic-photo{top:1016px;width:332px;height:225px}
.topic-card{top:1206px;width:298px;height:145px;background:var(--white);border-top:3px solid var(--pink);box-shadow:0 1px 5px rgba(0,0,0,.18);text-align:center}
.topic-card h3{font-family:"Quicksand",sans-serif;font-weight:600;color:var(--pink);font-size:22px;margin-top:22px}
.topic-card p{font-size:11.5px;line-height:25px;margin-top:6px;padding:0 10px}
.dot{top:1379px;width:16px;height:16px;border-radius:50%;background:#111}

/* mission */
.mission-title{left:545px;top:1698px;font-size:35px;color:var(--pink);font-family:"Quicksand",sans-serif;font-weight:500}
.mission-text{left:545px;top:1749px;width:575px;font-size:15px;line-height:35.5px;color:#444}

/* blog */
.post-photo{top:2349px;width:330px;height:194px}
.post-date{top:2526px;height:32px;width:116px;background:var(--pink-soft);color:var(--white);font-size:14px;display:flex;align-items:center;justify-content:center;gap:6px}
.post-meta{top:2575px;font-size:14px;color:#aaa;display:flex;gap:14px}
.post-title{top:2607px;font-size:18px;color:var(--pink);font-weight:500}
.post-text{top:2637px;width:332px;font-size:13px;line-height:25px;color:#333;text-align:justify}
.post-more{top:2693px;font-size:14px;color:var(--pink)}

/* newsletter */
.news-text{left:0;width:1200px;top:2972px;font-size:16px;line-height:35px;color:#333}
.field{height:36px;background:var(--white);border:1px solid #e2e2e2;font-size:11px;color:#555;display:flex;align-items:center;padding-left:16px;gap:6px}
.field-send{background:var(--pink);color:var(--white);justify-content:center;border:none;font-size:13px}

/* footer */
.site-footer{left:0;top:3269px;width:1200px;height:378px;background:var(--footer)}
.footer-social{top:3464px;width:30px;height:30px;border:1.5px solid #fff;border-radius:50%}
.footer-contact{left:0;width:1200px;top:3518px;color:#fff;font-size:17px;display:flex;justify-content:center;align-items:center;gap:12px}
.footer-nav{left:0;width:1200px;top:3560px;color:#fff;font-size:18px}
.copyright{left:0;width:1200px;top:3600px;color:#fff;font-size:12px}
</style>
</head>
<body>

<header class="site-header">
  <nav class="nav">
    <a style="left:89px">Make</a>
    <a style="left:166px">Save</a>
    <a style="left:236px">Spend</a>
    <a style="left:320px">Share</a>
    <a style="left:796px;top:58px">Mission</a>
    <a style="left:889px;top:58px">Get Started</a>
    <a style="left:1016px;top:58px">Contact BOL</a>
  </nav>
  <div class="brand-mark" style="left:572px;top:14px;width:56px;height:56px"></div>
  <div class="abs brand center header-brand">Blue Otter Lantern</div>
</header>

<!-- hero -->
<div class="abs hero"></div>
<div class="abs hero-photo" role="img" aria-label="Hand swinging a hammer at a pink piggy bank"></div>
<svg class="abs" style="left:0;top:640px" width="1200" height="140" viewBox="0 0 1200 140">
  <path d="M0 30 Q600 210 1200 30 L1200 140 L0 140Z" fill="#fff"/>
  <path d="M0 36 Q600 200 1200 36" fill="none" stroke="var(--pink-pale)" stroke-width="3"/>
  <path d="M20 48 Q600 190 1180 44 Q600 220 20 48Z" fill="var(--pink)"/>
</svg>
<div class="brand-mark" style="left:845px;top:262px;width:58px;height:58px"></div>
<div class="abs brand center hero-title">Blue Otter Lantern</div>
<p class="abs center hero-text">Lorem ipsum dolor sit amet, consectetur adipiscing elit, sed<br>do eiusmod tempor incididunt ut aliqua.</p>
<div class="btn" style="left:773px;top:462px;width:205px;height:54px;font-size:20px">Get Started
  <svg viewBox="0 0 20 20"><circle cx="10" cy="10" r="9" fill="#fff"/><path d="M5 10h8M10 6l4 4-4 4" stroke="#e34197" stroke-width="2.4" fill="none"/></svg></div>

<!-- welcome -->
<h1 class="abs section-title center" style="top:864px;font-size:37px">Welcome to <span style="color:var(--pink)">Blue Otter Lantern</span></h1>
<p class="abs center welcome-text">Sed ut perspiciatis unde omnis iste natus error sit voluptatem accusantium doloremque laudantium, totam rem aperiam, eaque ipsa<br>quae ab illo inventore veritatis et quasi architecto beatae vitae dicta sunt explicabo.</p>

<div class="abs topic-photo" style="left:77px;background:linear-gradient(135deg,#8a9bb0,#4e5d70)" role="img" aria-label="Team meeting around a table"></div>
<div class="abs topic-photo" style="left:435px;background:linear-gradient(135deg,#c9865c,#6e4a36)" role="img" aria-label="Couple putting a coin in a piggy bank"></div>
<div class="abs topic-photo" style="left:793px;background:linear-gradient(135deg,#9fb07a,#5f5046)" role="img" aria-label="Hands taking cash from a wallet"></div>

<div class="abs topic-card" style="left:94px"><h3>Make</h3><p>Sed ut perspiciatis unde omnis iste natus error sit voluptatem accusantium doloremque laudantium eaque veritatis&nbsp; vitae dicta sunt explicabo.</p></div>
<div class="abs topic-card" style="left:452px"><h3>Save</h3><p>Sed ut perspiciatis unde omnis iste natus error sit voluptatem accusantium doloremque laudantium eaque veritatis&nbsp; vitae dicta sunt explicabo.</p></div>
<div class="abs topic-card" style="left:810px"><h3>Spend</h3><p>Sed ut perspiciatis unde omnis iste natus error sit voluptatem accusantium doloremque laudantium eaque veritatis&nbsp; vitae dicta sunt explicabo.</p></div>

<div class="abs dot" style="left:569px"></div>
<div class="abs dot" style="left:592px;border:4px solid #111;background:#fff"></div>
<div class="abs dot" style="left:615px"></div>

<!-- mission -->
<svg class="abs" style="left:0;top:1490px" width="1200" height="700" viewBox="0 0 1200 700">
  <path d="M0 60 Q600 -30 1200 20 L1200 670 Q600 700 0 670Z" fill="var(--grey-band)"/>
  <path d="M0 60 Q300 20 600 12 Q300 30 0 96Z" fill="var(--pink)"/>
  <path d="M1200 596 Q900 640 600 680 Q900 680 1200 636Z" fill="var(--pink)"/>
</svg>
<svg class="abs" style="left:80px;top:1628px" width="420" height="430" viewBox="0 0 420 430">
  <path d="M20 130 A205 205 0 1 1 120 425" fill="none" stroke="var(--pink)" stroke-width="4"/>
</svg>
<div class="abs" style="left:92px;top:1648px;width:390px;height:390px;border-radius:50%;background:radial-gradient(circle at 55% 60%,#f4f2ef 0 22%,#c98a3a 40%,#7a4a1e 100%)" role="img" aria-label="Hand dropping a coin into a white piggy bank"></div>
<h2 class="abs mission-title">OUR MISSION</h2>
<p class="abs mission-text">I want to challenge you to rethink the way you think about growing, spending and saving money. By redesigning your life around your finances I want you to run your life as if you are the CEO of your own business, and the business is maximising the value and profitability of your life.</p>
<div class="btn" style="left:545px;top:1909px;width:205px;height:54px;font-size:18px;font-family:'Roboto',sans-serif;font-weight:500">About BOL
  <svg viewBox="0 0 20 20"><circle cx="10" cy="10" r="9" fill="#fff"/><path d="M5 10h8M10 6l4 4-4 4" stroke="#e34197" stroke-width="2.4" fill="none"/></svg></div>

<!-- blog -->
<h2 class="abs section-title center" style="top:2272px;font-size:35px;color:var(--pink)">OUR BLOG</h2>

<div class="abs post-photo" style="left:89px;background:linear-gradient(135deg,#b58a70,#5c3b2e)" role="img" aria-label="Family counting coins with a piggy bank"></div>
<div class="abs post-photo" style="left:434px;background:linear-gradient(135deg,#c7b6a4,#6c86a0)" role="img" aria-label="Parents and children saving coins together"></div>
<div class="abs post-photo" style="left:782px;background:linear-gradient(135deg,#d9c070,#e6b23a 50%,#9aa06a)" role="img" aria-label="Woman smiling beside a piggy bank"></div>

<div class="abs post-date" style="left:103px">&#9638; Oct 27 2018</div>
<div class="abs post-date" style="left:448px">&#9638; Oct 27 2018</div>
<div class="abs post-date" style="left:796px">&#9638; Oct 27 2018</div>

<div class="abs post-meta" style="left:89px"><span>&#9679; Comment(0)</span><span>&#9679; By Admin</span></div>
<div class="abs post-meta" style="left:434px"><span>&#9679; Comment(0)</span><span>&#9679; By Admin</span></div>
<div class="abs post-meta" style="left:782px"><span>&#9679; Comment(0)</span><span>&#9679; By Admin</span></div>

<h3 class="abs post-title" style="left:89px">SED UT PERSPICIATIS UND</h3>
<h3 class="abs post-title" style="left:434px">SED UT PERSPICIATIS UND</h3>
<h3 class="abs post-title" style="left:782px">SED UT PERSPICIATIS UND</h3>

<p class="abs post-text" style="left:89px">Sed ut perspiciatis unde omnis iste natus error sit voluptatem accusantium doloremque laudantium</p>
<p class="abs post-text" style="left:434px">Sed ut perspiciatis unde omnis iste natus error sit voluptatem accusantium doloremque laudantium</p>
<p class="abs post-text" style="left:782px">Sed ut perspiciatis unde omnis iste natus error sit voluptatem accusantium doloremque laudantium</p>

<a class="abs post-more" style="left:89px">READ MORE</a>
<a class="abs post-more" style="left:434px">READ MORE</a>
<a class="abs post-more" style="left:782px">READ MORE</a>

<!-- newsletter -->
<svg class="abs" style="left:0;top:2800px" width="1200" height="480" viewBox="0 0 1200 480">
  <path d="M0 10 Q600 -10 1200 100 L1200 480 L0 480Z" fill="var(--grey-band)"/>
  <path d="M640 20 Q950 40 1200 110 L1200 80 Q950 20 640 20Z" fill="var(--pink)"/>
  <path d="M0 380 Q300 470 600 470 L0 470Z" fill="var(--pink)"/>
  <path d="M0 430 Q300 470 600 470 Q900 480 1200 460 L1200 480 L0 480Z" fill="var(--footer)"/>
</svg>
<h2 class="abs section-title center" style="top:2918px;font-size:33px;color:var(--pink)">SUBSCRIBE TO NEWSLETTER</h2>
<p class="abs center news-text">We find that a phone chat is always the best way to get things started.<br>But if you can't talk now,send us your details and we'll happily call you at a timethat suits you.</p>
<div class="abs field" style="left:163px;top:3067px;width:428px">&#9679; NAME</div>
<div class="abs field" style="left:610px;top:3067px;width:429px">&#9742; CONTACT NUMBER</div>
<div class="abs field" style="left:163px;top:3122px;width:428px">&#9993; Email Address</div>
<div class="abs field field-send" style="left:610px;top:3122px;width:429px">&#10148; Yes, I want to Blue Otter Lantern</div>

<!-- footer -->
<footer class="abs site-footer"></footer>
<div class="brand-mark" style="left:575px;top:3340px;width:58px;height:58px"></div>
<div class="abs brand center" style="left:0;width:1200px;top:3404px;font-size:35px">Blue Otter Lantern</div>
<div class="abs footer-social" style="left:528px"></div>
<div class="abs footer-social" style="left:564px"></div>
<div class="abs footer-social" style="left:601px"></div>
<div class="abs footer-social" style="left:636px"></div>
<div class="abs footer-contact">
  <span>&#9742; Phone: 555 014 2276</span><span>|</span>
  <span>&#9993; Email: hello@blueotterlantern-sample.com</span><span>|</span>
  <span><svg width="12" height="16" viewBox="0 0 12 16"><path d="M6 0a6 6 0 0 0-6 6c0 4.5 6 10 6 10s6-5.5 6-10a6 6 0 0 0-6-6z" fill="#fff"/><circle cx="6" cy="6" r="2.2" fill="#231f20"/></svg> 42 Willow Bend Lane, Fairhaven, OR - 97000</span>
</div>
<div class="abs center footer-nav">Make &nbsp;|&nbsp; Save &nbsp;|&nbsp; Spend &nbsp;|&nbsp; Share &nbsp;|&nbsp; Mission &nbsp;|&nbsp; Get Started &nbsp;|&nbsp; Contact BOL</div>
<div class="abs center copyright">Copyrights &copy; 2019. All rights reserved.</div>

</body>
</html>
```